Criação de Layout de site para Computador & Internet
A empresa queria:
" Provedor de Internet banda larga para pessoas físicas e jurídicas com cobertura em duas cidades na região dos lagos, no Rio de Janeiro. "

```html
<!DOCTYPE html>
<html lang="pt-BR">
<head>
<meta charset="UTF-8">
<title>Fibra Óptica – Planos Empresariais</title>
<link rel="stylesheet" href="https://fonts.googleapis.com/css2?family=Montserrat:wght@400;500;600;700;800&display=swap">
<style>
  :root {
    --orange: #f47b20;
    --orange-deep: #e8680e;
    --orange-soft: #f9a25e;
    --band: #ececec;
    --white: #ffffff;
    --page: #ffffff;
  }
  * { box-sizing: border-box; margin: 0; padding: 0; }
  html, body { width: 1200px; height: 1200px; overflow: hidden; background: var(--page); }
  body { font-family: "Montserrat", sans-serif; color: var(--orange); position: relative; }

  .page-header { position: absolute; top: 250px; left: 0; width: 1200px; text-align: center; }
  .page-title { font-size: 52px; font-weight: 700; letter-spacing: -0.5px; color: var(--orange); }
  .page-subtitle { font-size: 30px; font-weight: 400; color: var(--orange-soft); margin-top: 2px; }

  .plans-band { position: absolute; top: 420px; left: 200px; width: 800px; height: 110px; background: var(--band); }

  .plans { position: absolute; top: 440px; left: 224px; width: 752px; display: flex; gap: 24px; }
  .plan-card {
    width: 170px; height: 320px; background: var(--orange);
    border-radius: 20px; border: 3px solid var(--white);
    box-shadow: 0 0 0 3px var(--orange);
    color: var(--white); text-align: center; padding-top: 16px;
  }
  .plan-tag { font-size: 9px; font-weight: 600; letter-spacing: 1px; opacity: .85; }
  .plan-speed { font-size: 50px; font-weight: 800; line-height: 1; margin-top: 2px; }
  .plan-unit { font-size: 15px; font-weight: 700; letter-spacing: 1px; }
  .plan-lead { font-size: 12px; font-weight: 700; line-height: 1.15; margin-top: 14px; }
  .plan-price { display: flex; justify-content: center; align-items: flex-start; margin-top: 4px; font-weight: 800; }
  .plan-price .currency { font-size: 10px; margin-top: 10px; margin-right: 2px; }
  .plan-price .amount { font-size: 38px; line-height: 1; }
  .plan-price .cents { font-size: 12px; margin-top: 4px; }
  .plan-button { width: 64px; height: 12px; background: var(--white); border-radius: 3px; margin: 6px auto 0; }
  .plan-divider { width: 130px; height: 1px; background: rgba(255,255,255,.6); margin: 18px auto 10px; }
  .plan-features { list-style: none; text-align: left; width: 112px; margin: 0 auto; font-size: 11px; font-weight: 500; line-height: 1.35; }
  .plan-features li::before { content: "• "; }

  .plan-notes { position: absolute; top: 812px; left: 200px; width: 820px; font-size: 12.5px; line-height: 1.55; color: var(--orange-soft); list-style: none; }
  .plan-notes li::before { content: "* "; }
  .plan-notes li:first-child::before { content: ""; }

  .closing-line { position: absolute; top: 920px; left: 0; width: 1200px; text-align: center; font-size: 19px; font-weight: 700; color: var(--orange); }
</style>
</head>
<body>
  <header class="page-header">
    <h1 class="page-title">Fibra Óptica</h1>
    <p class="page-subtitle">Planos Empresariais</p>
  </header>

  <div class="plans-band"></div>

  <section class="plans">
    <article class="plan-card">
      <p class="plan-tag">PLANO</p>
      <p class="plan-speed">350</p>
      <p class="plan-unit">MEGAS</p>
      <p class="plan-lead">POR<br>APENAS</p>
      <p class="plan-price"><span class="currency">R$</span><span class="amount">89</span><span class="cents">,90</span></p>
      <div class="plan-button"></div>
      <div class="plan-divider"></div>
      <ul class="plan-features"><li>100% Download</li><li>60% Upload</li><li>Suporte VIP</li></ul>
    </article>
    <article class="plan-card">
      <p class="plan-tag">PLANO</p>
      <p class="plan-speed">450</p>
      <p class="plan-unit">MEGAS</p>
      <p class="plan-lead">POR<br>APENAS</p>
      <p class="plan-price"><span class="currency">R$</span><span class="amount">99</span><span class="cents">,90</span></p>
      <div class="plan-button"></div>
      <div class="plan-divider"></div>
      <ul class="plan-features"><li>100% Download</li><li>60% Upload</li><li>Suporte VIP</li></ul>
    </article>
    <article class="plan-card">
      <p class="plan-tag">PLANO</p>
      <p class="plan-speed">500</p>
      <p class="plan-unit">MEGAS</p>
      <p class="plan-lead">POR<br>APENAS</p>
      <p class="plan-price"><span class="currency">R$</span><span class="amount">149</span><span class="cents">,90</span></p>
      <div class="plan-button"></div>
      <div class="plan-divider"></div>
      <ul class="plan-features"><li>100% Download</li><li>60% Upload</li><li>Suporte VIP</li></ul>
    </article>
    <article class="plan-card">
      <p class="plan-tag">PLANO</p>
      <p class="plan-speed">600</p>
      <p class="plan-unit">MEGAS</p>
      <p class="plan-lead">POR<br>APENAS</p>
      <p class="plan-price"><span class="currency">R$</span><span class="amount">159</span><span class="cents">,90</span></p>
      <div class="plan-button"></div>
      <div class="plan-divider"></div>
      <ul class="plan-features"><li>100% Download</li><li>60% Upload</li><li>Suporte VIP</li></ul>
    </article>
  </section>

  <ul class="plan-notes">
    <li>Os planos são válidos apenas para empresas.</li>
    <li>Todos os planos estão sujeitos à viabilidade técnica.</li>
    <li>O fornecimento de garantia de banda não se estende à entrega de sinais por meio do Wi-Fi.</li>
    <li>Para melhor experiência na utilização da conexão é necessário que o assinante possua equipamentos compatíveis com o plano contratado.</li>
  </ul>

  <p class="closing-line">Com a gente você terá o melhor serviço da região.</p>
</body>
</html>
```